Create a business promotion flyer to leave in customer mailboxes. We are a bulk petroleum supplier, servicing any industry that requires diesel. Base in griffith NSW, servicing griffith area and surrounds.

Business Name - Terra Diesel
Fuel@terradiesel-example.com.au
Owen - 0491 570 362 ohartley@terradiesel-example.com.au
Liam - 0491 570 718 lprosser@terradiesel-example.com.au
Simon - 0491 570 905 skenway@terradiesel-example.com.au
Office 02 5550 1734

Bulk Fuel deliveries.
Oils & lubricants
Local Family owned business

```html
<!DOCTYPE html>
<html lang="en">
<head>
<meta charset="utf-8">
<title>Terra Diesel – Bulk Petroleum Supplier Flyer</title>
<link rel="stylesheet" href="https://fonts.googleapis.com/css2?family=Montserrat:wght@600;700;800&family=Poppins:wght@500;600;700&family=Yellowtail&display=swap">
<style>
  :root{
    --stage:#a9a9a9;
    --paper-top:#f7f7f7;
    --paper-bottom:#fdeceb;
    --red:#ee2a1e;
    --dark:#3c3c3c;
    --white:#ffffff;
    --ring:#fbe3e1;
    --sky:#6f9fd8;
    --yard:#c9c6c0;
  }
  *{margin:0;padding:0;box-sizing:border-box}
  html,body{width:964px;height:1200px;overflow:hidden;background:var(--stage)}
  .flyer{
    position:absolute;left:172px;top:135px;width:620px;height:930px;overflow:hidden;
    background:linear-gradient(180deg,var(--paper-top) 0%,var(--paper-top) 40%,var(--paper-bottom) 100%);
    font-family:"Montserrat",sans-serif;color:var(--white);
  }
  .brand{position:absolute;left:42px;top:50px;display:flex;align-items:center;gap:12px}
  .brand-mark{width:34px;height:34px;border-radius:50%;background:var(--red)}
  .brand-name{font-family:"Poppins",sans-serif;font-weight:600;font-size:40px;color:var(--red);line-height:1}
  .shapes{position:absolute;left:0;top:0}
  .hero-photo,.fleet-photo{position:absolute}
  .hero-text{position:absolute;left:25px;top:148px}
  .hero-script{font-family:"Yellowtail",cursive;font-size:42px;line-height:1}
  .hero-big{font-weight:700;font-size:58px;line-height:1;margin-top:2px;letter-spacing:-1px}
  .hero-mid{font-weight:700;font-size:36px;line-height:1.15;margin-top:8px;letter-spacing:-0.5px}
  .hero-sub{font-family:"Poppins",sans-serif;font-weight:600;font-size:23px;line-height:1.2;margin-top:10px}
  .services-title{position:absolute;left:27px;top:440px;font-weight:800;font-size:39px;color:var(--dark);letter-spacing:-1px}
  .service{position:absolute;width:270px;height:97px}
  .service-pill{position:absolute;left:70px;top:0;right:0;height:97px;background:var(--dark);border-radius:0 49px 49px 0}
  .service-icon{position:absolute;left:-8px;top:-8px;width:113px;height:113px;border-radius:50%;background:var(--ring);display:flex;align-items:center;justify-content:center}
  .service-icon span{width:96px;height:96px;border-radius:50%;background:var(--red);display:flex;align-items:center;justify-content:center}
  .service-label{position:absolute;left:117px;top:0;height:97px;display:flex;align-items:center;font-family:"Poppins",sans-serif;font-weight:600;font-size:20px;line-height:1.3}
  .contact-title{position:absolute;left:28px;top:852px;font-weight:700;font-size:22px}
  .contact-email{position:absolute;left:28px;top:890px;display:flex;align-items:center;gap:8px;font-family:"Poppins",sans-serif;font-weight:600;font-size:12.5px;white-space:nowrap}
  .contact-phones{position:absolute;left:372px;top:843px;font-family:"Poppins",sans-serif;font-weight:700;font-size:18px;line-height:23px;white-space:nowrap}
  .phone-icon{position:absolute;left:342px;top:848px}
</style>
</head>
<body>
<main class="flyer">
  <div class="brand"><span class="brand-mark"></span><span class="brand-name">Terra Diesel</span></div>

  <svg class="shapes" width="620" height="930" viewBox="0 0 620 930">
    <path d="M620,97 H420 Q405,97 398,108 L300,280 L398,452 Q405,463 420,463 H620Z" fill="var(--red)"/>
    <path d="M0,138 H340 Q362,138 352,158 L282,280 L352,403 Q362,423 340,423 H0Z" fill="var(--red)"/>
    <rect x="233" y="833" width="387" height="97" fill="var(--red)"/>
    <path d="M0,849 H290 Q337,849 349,888 L361,930 H0Z" fill="var(--paper-bottom)"/>
    <path d="M0,849 H285 Q327,849 338,888 L350,930 H0Z" fill="var(--dark)"/>
  </svg>

  <svg class="hero-photo" style="left:0;top:0" width="620" height="930" viewBox="0 0 620 930" role="img" aria-label="Photo of fuel tanker trucks parked outside a depot shed under a blue sky">
    <defs>
      <linearGradient id="yardSky" x1="0" y1="0" x2="0" y2="1">
        <stop offset="0" stop-color="var(--sky)"/>
        <stop offset="0.42" stop-color="#dfe7ef"/>
        <stop offset="0.6" stop-color="#eceff1"/>
        <stop offset="1" stop-color="var(--yard)"/>
      </linearGradient>
    </defs>
    <path d="M620,108 H425 Q414,108 408,118 L314,280 L408,442 Q414,452 425,452 H620Z" fill="url(#yardSky)"/>
  </svg>

  <div class="hero-text">
    <div class="hero-script">We are</div>
    <div class="hero-big">A BULK</div>
    <div class="hero-mid">PETROLEUM<br>SUPPLIER</div>
    <div class="hero-sub">Servicing Any Industry<br>That Requires Diesel</div>
  </div>

  <h2 class="services-title">SERVICES</h2>

  <div class="service" style="left:26px;top:507px">
    <div class="service-pill"></div>
    <div class="service-icon"><span>
      <svg width="52" height="34" viewBox="0 0 52 34" fill="var(--white)"><rect x="0" y="4" width="32" height="16" rx="8"/><path d="M34,8 H44 L51,17 V26 H34Z"/><rect x="0" y="20" width="51" height="4"/><circle cx="8" cy="27" r="5"/><circle cx="20" cy="27" r="5"/><circle cx="43" cy="27" r="5"/></svg>
    </span></div>
    <div class="service-label">Bulk Fuel<br>Deliveries</div>
  </div>

  <div class="service" style="left:313px;top:507px">
    <div class="service-pill"></div>
    <div class="service-icon"><span>
      <svg width="40" height="44" viewBox="0 0 40 44" fill="var(--white)"><path d="M14,0 H26 V6 H14Z"/><path d="M8,8 H30 L34,14 V44 H2 V16Z"/><circle cx="26" cy="32" r="11" fill="var(--red)"/><path d="M26,24 Q32,32 32,35 A6,6 0 0 1 20,35 Q20,32 26,24Z"/></svg>
    </span></div>
    <div class="service-label">Oils &amp;<br>Lubricants</div>
  </div>

  <div class="service" style="left:26px;top:628px">
    <div class="service-pill"></div>
    <div class="service-icon"><span>
      <svg width="52" height="36" viewBox="0 0 52 36" fill="var(--white)"><rect x="2" y="0" width="14" height="18"/><rect x="18" y="0" width="14" height="18"/><path d="M34,8 H44 L51,18 V28 H34Z"/><rect x="0" y="20" width="51" height="5"/><circle cx="10" cy="29" r="5"/><circle cx="42" cy="29" r="5"/></svg>
    </span></div>
    <div class="service-label">Petrol<br>Deliveries</div>
  </div>

  <div class="service" style="left:313px;top:628px">
    <div class="service-pill"></div>
    <div class="service-icon"><span>
      <svg width="44" height="44" viewBox="0 0 44 44" fill="var(--white)"><path d="M22,0 L32,4 V12 Q32,20 22,24 Q12,20 12,12 V4Z"/><path d="M17,12 L21,16 L28,8" stroke="var(--red)" stroke-width="2.5" fill="none"/><circle cx="10" cy="28" r="4"/><circle cx="34" cy="28" r="4"/><circle cx="22" cy="30" r="4.5"/><path d="M2,44 Q2,34 10,34 Q16,34 17,40 V44Z"/><path d="M42,44 Q42,34 34,34 Q28,34 27,40 V44Z"/><path d="M14,44 Q14,36 22,36 Q30,36 30,44Z"/></svg>
    </span></div>
    <div class="service-label">Local<br>Family Owned<br>Business</div>
  </div>

  <svg class="fleet-photo" style="left:0;top:727px" width="620" height="106" viewBox="0 0 620 106" role="img" aria-label="Photo of a white road-train fuel tanker with red striping">
    <defs>
      <linearGradient id="fleetTone" x1="0" y1="0" x2="0" y2="1">
        <stop offset="0" stop-color="var(--paper-bottom)"/>
        <stop offset="0.3" stop-color="#f1f1f1"/>
        <stop offset="0.75" stop-color="#d9d9d9"/>
        <stop offset="1" stop-color="#8d8d8d"/>
      </linearGradient>
    </defs>
    <rect width="620" height="106" fill="url(#fleetTone)"/>
  </svg>

  <h3 class="contact-title">CONTACT US</h3>
  <div class="contact-email">
    <svg width="20" height="14" viewBox="0 0 20 14"><rect width="20" height="14" fill="var(--red)"/><path d="M0,0 L10,8 L20,0" stroke="var(--dark)" stroke-width="1.5" fill="none"/></svg>
    Fuel@terradiesel-example.com.au
  </div>

  <svg class="phone-icon" width="22" height="22" viewBox="0 0 24 24" fill="var(--white)"><path d="M6.6,10.8 C8,13.6 10.4,16 13.2,17.4 L15.4,15.2 C15.7,14.9 16.1,14.8 16.4,15 C17.5,15.4 18.7,15.6 20,15.6 C20.6,15.6 21,16 21,16.6 V20 C21,20.6 20.6,21 20,21 C10.6,21 3,13.4 3,4 C3,3.4 3.4,3 4,3 H7.5 C8.1,3 8.5,3.4 8.5,4 C8.5,5.3 8.7,6.5 9.1,7.6 C9.2,7.9 9.1,8.3 8.9,8.6Z"/></svg>
  <div class="contact-phones">
    <div>Owen - 0491 570 362</div>
    <div>Liam - 0491 570 718</div>
    <div>Simon - 0491 570 905</div>
  </div>
</main>
</body>
</html>
```